Redesign our Product Box!

We have a product box for our pet supplement we are looking to redesign. Please use the photoshop file of the current design for the logo/info/dieline and the concept picture of a bag we would like to see included in the box design.

Ideally the background will be the green with white text, but we really want it to be fun and appealing to pet owners so do not be scared to show your vision.

```html
<!DOCTYPE html>
<html lang="en">
<head>
<meta charset="utf-8">
<title>KelpyPaws Packaging</title>
<link href="https://fonts.googleapis.com/css2?family=Source+Sans+3:wght@300;400;600;700;900&display=swap" rel="stylesheet">
<style>
  :root {
    --mint: #b8f3d3;
    --bag-green: #2fa84d;
    --box-green: #00a650;
    --cut: #c0392b;
    --fold: #3355aa;
    --ink: #333333;
    --silver: #d9d9d9;
    --white: #ffffff;
    --photo-warm: #d9b48f;
    --photo-grey: #b9b9b9;
  }
  html, body { margin: 0; padding: 0; width: 1200px; height: 2354px; overflow: hidden; background: var(--white); }
  .sheet { display: block; width: 1200px; height: 2354px; font-family: "Source Sans 3", sans-serif; }
  .backdrop { fill: var(--mint); }
  .bag { fill: var(--bag-green); }
  .bag-count { fill: var(--white); font-weight: 700; }
  .bag-ring { fill: none; stroke: var(--white); stroke-width: 2; stroke-dasharray: 8 6; }
  .bag-name { fill: var(--silver); font-weight: 700; font-size: 84px; }
  .photo-warm { fill: var(--photo-warm); }
  .photo-grey { fill: var(--photo-grey); }
  .panel { fill: var(--white); stroke: var(--fold); stroke-width: 1.5; }
  .flap { fill: var(--box-green); stroke: var(--cut); stroke-width: 1.5; }
  .flap-white { fill: var(--white); stroke: var(--cut); stroke-width: 1.5; }
  .band { fill: var(--box-green); }
  .brand { fill: var(--box-green); font-weight: 700; font-size: 42px; }
  .copy { fill: var(--ink); font-weight: 300; }
  .copy-bold { fill: var(--ink); font-weight: 600; }
  .on-green { fill: var(--white); font-weight: 400; }
  .print-side { fill: var(--ink); font-weight: 400; font-size: 42px; }
  .facts-box { fill: var(--white); stroke: var(--ink); stroke-width: 1.5; }
  .facts-rule { stroke: var(--ink); stroke-width: 1.5; }
  .facts-title { fill: #000; font-weight: 900; font-size: 30px; }
  .tiny { fill: var(--ink); font-size: 7px; font-weight: 400; }
  .small { fill: #000; font-size: 10px; font-weight: 400; }
  .divider { stroke: #9bbf3b; stroke-width: 1.5; }
</style>
</head>
<body>
<svg class="sheet" viewBox="0 0 1300 2550" xmlns="http://www.w3.org/2000/svg">

  <!-- Pouch artwork, flat -->
  <g class="pouch">
    <rect class="backdrop" x="112" y="148" width="1088" height="955"/>
    <rect class="bag" x="327" y="240" width="486" height="790"/>
    <circle class="bag-ring" cx="590" cy="637" r="66"/>
    <text class="bag-count" x="590" y="650" text-anchor="middle" font-size="62">30</text>
    <text class="bag-count" x="590" y="675" text-anchor="middle" font-size="20" font-weight="600">Servings</text>
    <rect class="photo-warm" x="372" y="785" width="292" height="245" rx="6" role="img" aria-label="Photo of a kitten beside a dog wearing a stethoscope"/>
    <text class="bag-name" transform="translate(732 990) rotate(-90)">KelpyPaws™</text>
  </g>

  <!-- Box dieline -->
  <g class="dieline">
    <text class="print-side" x="800" y="1460">PRINT</text>
    <text class="print-side" x="800" y="1512">SIDE</text>

    <!-- top tuck flap and lid -->
    <path class="flap-white" d="M147 1335 C147 1290 170 1243 192 1243 L400 1243 C425 1243 448 1290 448 1335 Z"/>
    <rect class="panel" x="143" y="1335" width="307" height="247"/>
    <text class="brand" x="296" y="1410" text-anchor="middle">KelpyPaws</text>
    <rect class="photo-warm" x="188" y="1430" width="220" height="130" rx="6" role="img" aria-label="Photo of a puppy and a kitten lying together"/>

    <!-- glue flap -->
    <path class="flap-white" d="M143 1584 L65 1592 L65 2130 L143 2138 Z"/>

    <!-- dust flaps top -->
    <path class="flap" d="M452 1413 L665 1413 L680 1555 L693 1582 L452 1582 Z"/>
    <path class="flap" d="M1035 1413 L1247 1413 L1247 1582 L1008 1582 L1022 1555 Z"/>

    <!-- front panel -->
    <rect class="panel" x="143" y="1582" width="307" height="556"/>
    <text class="brand" x="294" y="1650" text-anchor="middle">KelpyPaws</text>
    <rect class="band" x="143" y="1670" width="307" height="83"/>
    <text class="on-green" x="296" y="1704" text-anchor="middle" font-size="27">100% Pure Marine</text>
    <text class="on-green" x="296" y="1740" text-anchor="middle" font-size="27">Phytoplankton Powder</text>
    <text class="copy" x="296" y="1786" text-anchor="middle" font-size="21" font-weight="400">Foundational Nutrition</text>
    <text class="copy" x="296" y="1815" text-anchor="middle" font-size="21" font-weight="400">&amp; Super-Antioxidant</text>
    <text class="copy" x="162" y="1877" font-size="21" font-weight="400">For Dogs &amp;</text>
    <text class="copy" x="162" y="1906" font-size="21" font-weight="400">Cats</text>
    <rect class="photo-grey" x="150" y="1835" width="292" height="243" rx="6" role="img" aria-label="Photo of a grey cat and a husky lying together"/>
    <rect class="band" x="143" y="2080" width="307" height="58"/>
    <text class="on-green" x="296" y="2103" text-anchor="middle" font-size="16">15g</text>

    <!-- directions panel -->
    <rect class="panel" x="450" y="1582" width="247" height="556"/>
    <g class="copy" font-size="15" text-anchor="middle">
      <text x="574" y="1617">Directions: For dogs &amp; cats</text>
      <text x="574" y="1638">1/16tsp once per day.</text>
      <text x="574" y="1659">Administer orally. To be mixed</text>
      <text x="574" y="1680">into food. 1/16tsp = 1/2 the</text>
      <text x="574" y="1701">included scoop.</text>
    </g>
    <line class="divider" x1="488" y1="1731" x2="660" y2="1731"/>
    <text class="copy-bold" x="574" y="1756" text-anchor="middle" font-size="17" font-weight="400">Unlock Nature’s</text>
    <text class="copy-bold" x="574" y="1780" text-anchor="middle" font-size="17" font-weight="400">Nutrient Treasure:</text>
    <g class="copy" font-size="14" text-anchor="middle">
      <text x="574" y="1817">Phytoplankton is the foundation of</text>
      <text x="574" y="1838">life, It is the first plant in the entire</text>
      <text x="574" y="1859">food chain.</text>
      <text x="574" y="1900">Phytoplankton is a microscopic</text>
      <text x="574" y="1921">powerhouse. Your pet’s body</text>
      <text x="574" y="1942">absorbs billions of phytoplankton</text>
      <text x="574" y="1963">with every serving.</text>
      <text x="574" y="2004">Packed with the building blocks of</text>
      <text x="574" y="2025">life, phytoplankton addresses</text>
      <text x="574" y="2046">multiple aspects of your pet’s</text>
      <text x="574" y="2067">health in one simple supplement.</text>
    </g>
    <rect class="band" x="450" y="2080" width="247" height="58"/>

    <!-- facts panel -->
    <rect class="panel" x="697" y="1582" width="308" height="556"/>
    <rect class="facts-box" x="713" y="1606" width="277" height="144"/>
    <text class="facts-title" x="846" y="1634" text-anchor="middle">Supplement Facts</text>
    <line class="facts-rule" x1="713" y1="1643" x2="990" y2="1643"/>
    <text class="small" x="730" y="1659">Serving Size: 1 Scoop/Day</text>
    <text class="small" x="730" y="1670">Servings per Container: 30</text>
    <text class="small" x="865" y="1670">Amount per Serving</text>
    <text class="small" x="958" y="1670">%DV</text>
    <line class="facts-rule" x1="713" y1="1680" x2="990" y2="1680"/>
    <text class="small" x="730" y="1702">Microalgae Nannochloropsis Gaditana</text>
    <text class="small" x="922" y="1702">500mg</text>
    <text class="small" x="967" y="1702">‡</text>
    <line class="facts-rule" x1="713" y1="1720" x2="990" y2="1720"/>
    <text class="small" x="730" y="1738">‡ Daily value not established.</text>
    <text class="tiny" x="713" y="1763">These statements have not been evaluated by the Food and Drug Administrations.</text>
    <text class="tiny" x="713" y="1773">This products is not intended to diagnose, treat, cure, or prevent any disease.</text>
    <text class="tiny" x="713" y="1794">Store in a cool, dry place.</text>
    <g class="copy" font-size="14" font-weight="400">
      <text x="715" y="1830" font-weight="600">Distributed By::</text>
      <text x="715" y="1848">Marinova Pet Labs Inc.</text>
      <text x="715" y="1866">412 Harbour Road,</text>
      <text x="715" y="1884">Saltcove, Nova Scotia Canada</text>
      <text x="715" y="1902">B0J 2K0</text>
    </g>
    <g class="copy" font-size="8.5" font-weight="400">
      <text x="714" y="1921">Warnings: Check with a qualified healthcare professional before</text>
      <text x="714" y="1931">using this product if you are pregnant, breastfeeding, or taking</text>
      <text x="714" y="1941">blood thinners. You should call your doctor for medical advice</text>
      <text x="714" y="1951">about serious adverse events. To report a serious adverse event</text>
      <text x="714" y="1961">or obtain product information contact:  1 800 555 0142</text>
    </g>
    <rect class="photo-warm" x="700" y="1985" width="300" height="95" rx="4" role="img" aria-label="Photo of a row of dogs and cats peeking over the edge"/>
    <rect class="band" x="697" y="2080" width="308" height="58"/>
    <text class="on-green" x="851" y="2105" text-anchor="middle" font-size="16">Customer Care: 1 800 555 0142</text>
    <text class="on-green" x="851" y="2126" text-anchor="middle" font-size="16">marinovapetlabs.example</text>

    <!-- story panel -->
    <rect class="panel" x="1005" y="1582" width="242" height="556"/>
    <g class="copy" font-size="14.5" text-anchor="middle">
      <text x="1124" y="1617">Our premium phytoplankton</text>
      <text x="1124" y="1638">powder is a extraordinary</text>
      <text x="1124" y="1659">supplement.  It infuses your pet’s</text>
      <text x="1124" y="1680">body with pure, plant-based</text>
      <text x="1124" y="1701">nutrients and potent antioxidants.</text>
      <text x="1124" y="1742">Phytoplankton goes beyond</text>
      <text x="1124" y="1763">ordinary supplements; it’s a path</text>
      <text x="1124" y="1784">to optimal health. In just a few</text>
      <text x="1124" y="1805">weeks, your pet will experience a</text>
      <text x="1124" y="1826">feeling of calm and strength, the</text>
      <text x="1124" y="1847">kind of wellness our customers</text>
      <text x="1124" y="1868">often say they've been seeking.</text>
      <text x="1124" y="1909">Join those who have discovered</text>
      <text x="1124" y="1930">the transformative power of</text>
      <text x="1124" y="1951">phytoplankton. See the difference</text>
      <text x="1124" y="1972">for yourself and understand why</text>
      <text x="1124" y="1993">it's not just a supplement, but a</text>
      <text x="1124" y="2014">revolution in pet health and</text>
      <text x="1124" y="2035">vitality.</text>
    </g>
    <rect class="photo-warm" x="1010" y="2030" width="32" height="50" rx="3" role="img" aria-label="Photo of a kitten peeking in"/>
    <rect class="photo-warm" x="1186" y="2015" width="58" height="65" rx="3" role="img" aria-label="Photo of a puppy and kitten peeking in"/>
    <rect class="band" x="1005" y="2080" width="242" height="58"/>

    <!-- bottom flaps -->
    <path class="flap" d="M452 2138 L695 2138 L695 2308 L482 2308 L470 2170 L455 2155 Z"/>
    <path class="flap" d="M1005 2138 L1247 2138 L1247 2155 L1232 2170 L1220 2308 L1005 2308 Z"/>
    <path class="flap" d="M697 2138 L1005 2138 L1005 2385 C1005 2430 980 2480 955 2480 L748 2480 C722 2480 697 2430 697 2385 Z"/>
    <line x1="697" y1="2385" x2="1005" y2="2385" stroke="var(--fold)" stroke-width="1.5"/>
    <text class="on-green" transform="translate(851 2350) rotate(180)" text-anchor="middle" font-size="17" fill="#1a1a1a" style="fill:#1a1a1a">Exp: 22025/03/Lot No.:12222</text>
  </g>
</svg>
</body>
</html>
```